nutrition company business card

I would like to have a business card that has two sides, one being the green color from the Company name on the logo. I am open to ideas and looks that work with my logo. I like the idea of having a negative image of the tree on the green side.

For my information on the card I must have:
Megan Colbrook
415-555-0172
megancolbrook@quillpost.example

This area will need to be updated once I complete my schooling.

Reason: I need to extend my deadline by one day as I have been sick the last week and not had time to review all the new designs. Thank you.

Industry/Entity Type

Nutrition

Requirements
Must have
• I would like to have a business card that has two sides, one being the green color from the Company name on the logo. I am open to ideas and looks that work with my logo. I like the idea of having a negative image of the tree on the green side.
• For my information on the card I must have:
• Megan Colbrook
• 415-555-0172
• megancolbrook@quillpost.example
• This area will need to be updated once I complete my schooling.

```html
<!DOCTYPE html>
<html lang="en">
<head>
<meta charset="utf-8">
<title>Rooted Table – Business Card</title>
<link rel="stylesheet" href="https://fonts.googleapis.com/css2?family=Questrial&display=swap">
<style>
  :root {
    --backdrop: #e4e2de;
    --brand-green: #7cb32a;
    --leaf-light: #9cc65a;
    --paper: #ededec;
    --leaf-pale: #cfe0b4;
    --taupe: #8a7a70;
    --ink-grey: #8b8b8b;
    --white: #ffffff;
  }
  * { box-sizing: border-box; margin: 0; padding: 0; }
  html, body {
    width: 1200px;
    height: 900px;
    overflow: hidden;
    background: var(--backdrop);
    font-family: "Questrial", "Century Gothic", sans-serif;
  }
  .canvas {
    width: 1200px;
    height: 900px;
    display: flex;
    flex-direction: column;
    align-items: center;
    justify-content: center;
    gap: 40px;
  }
  .card {
    position: relative;
    width: 700px;
    height: 400px;
    overflow: hidden;
    box-shadow: 0 6px 18px rgba(0,0,0,0.12);
  }

  /* Front side */
  .card--front { background: var(--brand-green); }
  .foliage { position: absolute; }
  .card--front .foliage--top-right {
    top: 0; right: 0; width: 240px; height: 120px;
    background: radial-gradient(ellipse at 70% 20%, rgba(156,198,90,0.75), rgba(156,198,90,0) 70%);
  }
  .card--front .foliage--bottom-left {
    bottom: 0; left: 0; width: 280px; height: 190px;
    background: radial-gradient(ellipse at 25% 75%, rgba(156,198,90,0.75), rgba(156,198,90,0) 70%);
  }
  .front-brand {
    position: absolute;
    top: 62px; left: 0; right: 0;
    display: flex; flex-direction: column; align-items: center;
    color: var(--white);
  }
  .brand-mark {
    width: 116px; height: 116px;
    border-radius: 50%;
    border: 4px solid var(--white);
  }
  .front-brand .brand-name {
    margin-top: 34px;
    font-size: 56px;
    line-height: 1;
    letter-spacing: 0.5px;
  }
  .front-brand .tagline {
    margin-top: 4px;
    font-size: 27px;
    letter-spacing: 1.5px;
    opacity: 0.95;
  }

  /* Back side */
  .card--back { background: var(--paper); }
  .card--back .foliage--top-right {
    top: 0; right: 0; width: 260px; height: 150px;
    background: radial-gradient(ellipse at 65% 35%, var(--leaf-pale), rgba(207,224,180,0) 70%);
  }
  .card--back .foliage--bottom-left {
    bottom: 40px; left: 0; width: 290px; height: 210px;
    background: radial-gradient(ellipse at 30% 65%, var(--leaf-pale), rgba(207,224,180,0) 70%);
  }
  .back-brand {
    position: absolute;
    top: 52px; left: 250px;
    width: 260px;
    display: flex; flex-direction: column; align-items: center;
  }
  .back-brand .brand-mark {
    width: 84px; height: 84px;
    border: 4px solid var(--taupe);
  }
  .back-brand .brand-name {
    margin-top: 10px;
    font-size: 36px;
    line-height: 1;
    color: var(--brand-green);
  }
  .back-brand .tagline {
    margin-top: 2px;
    font-size: 17px;
    letter-spacing: 1.2px;
    color: var(--ink-grey);
    white-space: nowrap;
  }
  .contact {
    position: absolute;
    top: 226px; left: 300px;
    color: var(--taupe);
  }
  .contact .person-name {
    font-size: 27px;
    letter-spacing: 0.5px;
    text-transform: uppercase;
    margin-bottom: 14px;
  }
  .contact-line {
    display: flex;
    align-items: baseline;
    gap: 12px;
    font-size: 18px;
    line-height: 1.5;
  }
  .contact-line .label {
    width: 14px;
    color: var(--brand-green);
  }
  .contact-line--phone { padding-left: 20px; }
  .band {
    position: absolute;
    left: 0; right: 0; bottom: 20px;
    height: 18px;
    background: var(--brand-green);
  }
</style>
</head>
<body>
  <main class="canvas">
    <section class="card card--front" aria-label="Business card front">
      <div class="foliage foliage--top-right" role="img" aria-label="Negative tree leaf pattern"></div>
      <div class="foliage foliage--bottom-left" role="img" aria-label="Negative tree leaf pattern"></div>
      <div class="front-brand">
        <div class="brand-mark"></div>
        <div class="brand-name">Rooted Table</div>
        <div class="tagline">good food, simply shared</div>
      </div>
    </section>

    <section class="card card--back" aria-label="Business card back">
      <div class="foliage foliage--top-right" role="img" aria-label="Pale green tree branch with leaves"></div>
      <div class="foliage foliage--bottom-left" role="img" aria-label="Pale green tree branch with leaves"></div>
      <div class="back-brand">
        <div class="brand-mark"></div>
        <div class="brand-name">Rooted Table</div>
        <div class="tagline">good food, simply shared</div>
      </div>
      <div class="contact">
        <div class="person-name">Megan Colbrook</div>
        <div class="contact-line contact-line--phone"><span class="label">T</span><span class="value">415-555-0172</span></div>
        <div class="contact-line"><span class="label">E</span><span class="value">megancolbrook@quillpost.example</span></div>
      </div>
      <div class="band"></div>
    </section>
  </main>
</body>
</html>
```